Vantoq Business Card Project showing the logo and a marbo image on the rear

Design a whacky but professional business card, the logo is for the front and the Marbo image is for the rear. Happy to consider other open source Marbo Images if the designer wants to select one from the web. Vantoq is a competitor to OMB.com.au and Pellory.com.au and is based around every property in Australia

Target Market(s)

Business

Contact Information for Business Card

Name, Title, Email, Web, Phone Number

Font styles to use
Other font styles liked:
• avenir

Requirements
Must have
• Image on Back logo on front
Nice to have
• Happy to consider other images on rear, preftably Colin Marbo. Image supplied I own, we can use open source other Marbo Images

```html
<!DOCTYPE html>
<html lang="en">
<head>
<meta charset="utf-8">
<title>Vantoq Business Card</title>
<link rel="stylesheet" href="https://fonts.googleapis.com/css2?family=Roboto:wght@400;500;700&display=swap">
<style>
  :root {
    --page-bg: #d9dcde;
    --card-face: #eef0f1;
    --panel-dark: #1c1c1e;
    --brand-orange: #f0920f;
    --brand-orange-deep: #e07f05;
    --text-dark: #1f1f1f;
    --text-light: #fdf1e0;
    --logo-white: #f7f4f1;
  }
  * { margin: 0; padding: 0; box-sizing: border-box; }
  html, body {
    width: 1200px; height: 1054px; overflow: hidden;
    background: var(--page-bg);
    font-family: "Roboto", Arial, sans-serif;
  }
  .business-card {
    position: absolute; left: 100px; top: 226px;
    width: 1000px; height: 602px;
    border-radius: 28px; overflow: hidden;
    background: var(--card-face);
    box-shadow: 0 10px 30px rgba(0,0,0,0.18);
  }
  .card-shapes { position: absolute; inset: 0; }
  .brand-lockup {
    position: absolute; left: 80px; top: 392px; width: 310px;
    display: flex; align-items: center; justify-content: center; gap: 16px;
  }
  .brand-mark { width: 26px; height: 26px; background: var(--brand-orange); }
  .brand-name {
    font-size: 58px; font-weight: 500; color: var(--logo-white);
    letter-spacing: 1px; line-height: 1;
  }
  .contact-block { position: absolute; left: 597px; top: 108px; color: var(--text-dark); }
  .person-name { font-size: 35px; font-weight: 500; color: var(--brand-orange); line-height: 1.1; }
  .person-title { font-size: 23px; margin-top: 8px; }
  .contact-list { list-style: none; margin-top: 46px; }
  .contact-list li {
    display: flex; align-items: center; gap: 18px;
    font-size: 24px; height: 38px;
  }
  .contact-list svg { width: 24px; height: 24px; flex: none; }
  .web-highlight { color: var(--brand-orange); }
  .postal-address { font-size: 23px; line-height: 32px; margin-top: 22px; }
  .tagline-band {
    position: absolute; left: 440px; top: 506px; width: 560px; height: 60px;
    background: linear-gradient(90deg, var(--brand-orange-deep), var(--brand-orange));
    display: flex; align-items: center; justify-content: center;
    color: var(--text-light); font-size: 23px; padding-left: 30px;
  }
</style>
</head>
<body>
  <div class="business-card">
    <svg class="card-shapes" viewBox="0 0 1000 602" width="1000" height="602" aria-hidden="true">
      <path d="M0,0 H440 C600,170 590,460 430,602 H0 Z" fill="var(--brand-orange)"/>
      <path d="M0,0 H410 C565,130 560,470 395,602 H0 Z" fill="var(--panel-dark)"/>
    </svg>

    <div class="tagline-band">Buying, Selling and Research</div>

    <div class="brand-lockup">
      <span class="brand-mark"></span>
      <span class="brand-name">Vantoq</span>
    </div>

    <div class="contact-block">
      <div class="person-name">Dean Calloway</div>
      <div class="person-title">Founder &amp; CEO</div>
      <ul class="contact-list">
        <li>
          <svg viewBox="0 0 24 24"><circle cx="12" cy="12" r="9" fill="none" stroke="var(--brand-orange)" stroke-width="2"/><path d="M9 8 l2 2 -1 1.5 c1 1.5 2 2.5 3.5 3.5 l1.5-1 2 2 -1.5 1.5 c-3-0.5-7-4.5-7.5-7.5 z" fill="var(--brand-orange)"/></svg>
          <span>(00) 4444 5555</span>
        </li>
        <li>
          <svg viewBox="0 0 24 24"><rect x="3" y="6" width="18" height="12" fill="var(--brand-orange)"/><path d="M3 6 L12 13 L21 6" fill="none" stroke="var(--card-face)" stroke-width="1.6"/></svg>
          <span>calloway@vantoq.com</span>
        </li>
        <li>
          <svg viewBox="0 0 24 24"><circle cx="12" cy="12" r="9" fill="var(--brand-orange)"/><path d="M3 12 H21 M12 3 C8 7 8 17 12 21 M12 3 C16 7 16 17 12 21" fill="none" stroke="var(--card-face)" stroke-width="1.3"/></svg>
          <span>www.<span class="web-highlight">vantoq</span>.com</span>
        </li>
      </ul>
      <p class="postal-address">Level 4, 18 Harlow Street,<br>Sydney 2000, Australia</p>
    </div>
  </div>
</body>
</html>
```